High Tech Real Estate Startup needs a business card

We are developing an innovative real estate marketing product based around advanced search and virtual reality.

We talk to people, we need business cards.

Target Market(s)

The target market is technology professionals and realtors.

Contact Information for Business Card

The information to be included will include

Name
Title
Phone Number
E-mail Address
www.zelquin.com

It should use simple iconography for each one of those fields.

Font styles to use
Other font styles liked:
• Co, Jubilat, Avenir

Colors

Designer to choose colors to be used in the design.

Requirements
Must have
• Clean aesthetic,
• Good use of negative space.
• It should use our company logo, shown in the attached file. It is able to use the negative of that logo (coloured font and white background) and I have attached other acceptable accent colours in a swatch file.
Should not have
• Should not be too busy
• No extraneous text (slogans, tag lines etc)

```html
<!DOCTYPE html>
<html lang="en">
<head>
<meta charset="utf-8">
<title>Zelquin Business Card</title>
<link href="https://fonts.googleapis.com/css2?family=Nunito+Sans:wght@400;600;700;800&display=swap" rel="stylesheet">
<style>
  :root {
    --teal: #00b6bd;
    --teal-dark: #009ea5;
    --white: #ffffff;
    --backdrop: #2a2a2c;
    --card-size: 420px;
    --radius: 30px;
  }
  * { box-sizing: border-box; margin: 0; padding: 0; }
  html, body {
    width: 1200px; height: 800px; overflow: hidden;
    background: var(--backdrop);
    font-family: "Nunito Sans", "Helvetica Neue", Arial, sans-serif;
  }
  .stage {
    width: 1200px; height: 800px;
    display: flex; align-items: center; justify-content: center; gap: 80px;
  }
  .card {
    width: var(--card-size); height: var(--card-size);
    border-radius: var(--radius);
    overflow: hidden; position: relative;
  }
  .card--front {
    background: var(--teal);
    display: flex; align-items: center; justify-content: center;
  }
  .wordmark {
    font-weight: 600; letter-spacing: 0.14em; line-height: 1;
  }
  .card--front .wordmark { color: var(--white); font-size: 60px; }
  .card--back { background: var(--white); }
  .card--back .wordmark {
    color: var(--teal); font-size: 50px;
    position: absolute; top: 62px; right: 44px;
  }
  .contact {
    position: absolute; right: 48px; top: 140px; width: 260px;
    text-align: right; color: var(--teal);
  }
  .contact__name { font-size: 18px; font-weight: 800; letter-spacing: 0.04em; }
  .contact__title { font-size: 15px; font-weight: 400; margin-top: 2px; }
  .contact__rule { height: 1px; background: var(--teal); margin: 12px 0 10px; }
  .contact__label { font-size: 11px; font-weight: 800; color: var(--teal-dark); margin-top: 6px; }
  .contact__value { font-size: 16px; font-weight: 400; }
  .web-band {
    position: absolute; left: 0; right: 0; bottom: 0; height: 66px;
    background: var(--teal); color: var(--white);
    display: flex; align-items: center; justify-content: center;
    font-size: 17px; letter-spacing: 0.12em;
  }
</style>
</head>
<body>
  <main class="stage">
    <section class="card card--front" aria-label="Card front">
      <span class="wordmark">ZELQUIN</span>
    </section>
    <section class="card card--back" aria-label="Card back">
      <span class="wordmark">ZELQUIN</span>
      <div class="contact">
        <p class="contact__name">DARO KESTLIN</p>
        <p class="contact__title">Manager</p>
        <div class="contact__rule"></div>
        <p class="contact__label">Phone</p>
        <p class="contact__value">555-014-2290</p>
        <p class="contact__label">Email</p>
        <p class="contact__value">info@zelquinmail.com</p>
        <div class="contact__rule"></div>
      </div>
      <div class="web-band">www.zelquin.com</div>
    </section>
  </main>
</body>
</html>
```